Zing Webcomic

A simple signup landing page and blog design for an upcoming webcomic. I am mostly looking for a flat UI with a simple color scheme. I want to showcase a large background image and the comic title image. I have all the technicals figured out (I am a web developer by trade), so all I need now is a solid design I like.

The signup for should only have one field (email) and have text above it, and smaller text below it.

The blog, I am thinking, should be in the style of comic book pages. The home page would be blocks with large white outlines, with the article pages being an extension of that. As I stated before, should be fairly minimalist, but fun. Also, no sidebar or ads, IE single column. I have attached a simple mockup/layout of the blog to give a general idea of what I am going for.

I have attached the Logo and Background art (uncolored) for reference. Don't worry about the background image blending in, I can take care of that when the design is implemented. I will be focusing on layout and overall look, not necessarily readability (which I can fix).

~Please DO NOT take these examples literally. I will describe what I like about each example.~

Signup pages:
http://example-plaza.test/landing-page-type-photo/
http://www.lanternhop.test/showcase/website-design/814/10-most-beautiful-landing-pages-in-minimalist-style
http://quillnest.test/47-modern-landing-pages-showcasing-inspirational-web-design/
Great examples of minimalist design. However, instead of text or other content, there should be a simple signup form, as described above. Also think a lot more "playful" rather than super professional.

Blog:
http://vrakk.test/
Awesome example of a single column, minimal design. Needs to be more "comicbook style" though.
http://tidyrows.test/
Another good example of minimal design blog.
http://makerbarn.test/wp-content/uploads/res-blogs-5.jpg
I like the timeline feel here. Combine that with a comic book page kind of thing, and I think you have a winner.

Actual webcomic landing (not required):
http://www.lunarfoxpanels.test/comic.php?date=20021104#.U90ysYBdUvU
I like the navigation. It makes the atmosphere nice for the comic. The page layout itself is WAY too busy.
http://www.dime-galaxy.test/comic/
Fairly common webcomic, but their navigation and page layout is nice.
http://qvmp.test/936/
Another common webcomic. The simple page layout makes it easy for people to get started I think.

So there you have it. I will try my best to keep updating and adding to the description. If you have any questions, please don't hesitate to ask.
Updates

Hey Guys, I am really appreciating all the effort you have been putting in. I am amazed to see all the awesome designs and all the care taken with the project. I am just writing everyone to let you know that I have uploaded a simple layout/wireframe of the blog, to give an idea of what I am going for. Can't wait to see how things progress, and good luck to everyone!

Industry/Entity Type

Trade

Font styles to use
Sans Serif

Requirements
Must have
• Must showcase a large background image (does not have to cover the entire background). Should be a flat UI as well. Should be mostly neutral with splashes of blue or purple. Social links should also be somewhere (twitter, facebook, etc.).
Nice to have
• I am thinking something with rounded boxes, but I can live without them. A more "fun" design as opposed to more professional is definitely nice to have.

If you would like to try a stab at the actual comic page display and navigation, you are welcome to submit something. It should not be a main priority though.

Being responsive is not a requirement, but it would be nice to have.
Should not have
• A billion links in the navigation or look too busy.
No sidebar or advertisements. Should be a clean design.

```html
<!DOCTYPE html>
<html lang="en">
<head>
<meta charset="utf-8">
<title>Zing Webcomic — Sign up</title>
<link rel="stylesheet" href="https://fonts.googleapis.com/css2?family=Noto+Serif:wght@700&family=Raleway:wght@400;500;600;700;800&display=swap">
<style>
  :root {
    --bg-deep: #111111;
    --bg-shadow: #1b1b1b;
    --bg-mid: #2b2b2b;
    --bg-light: #3c3c3c;
    --bg-highlight: #474747;
    --text-white: #ffffff;
    --text-muted: #d8d8d8;
    --field-bg: #ffffff;
    --placeholder: #9a9a9a;
    --accent-purple: #b85ce6;
    --icon-grey: #8f8f8f;
    --icon-glyph: #262626;
  }
  * { box-sizing: border-box; margin: 0; padding: 0; }
  html, body { width: 1200px; height: 676px; overflow: hidden; background: var(--bg-deep); }
  .landing {
    position: relative;
    width: 1200px;
    height: 676px;
    overflow: hidden;
    font-family: "Raleway", sans-serif;
    color: var(--text-white);
  }
  .hero-art {
    position: absolute;
    inset: 0;
    background:
      radial-gradient(ellipse 22% 26% at 48% 22%, var(--bg-highlight) 0%, transparent 70%),
      radial-gradient(ellipse 20% 22% at 82% 24%, var(--bg-light) 0%, transparent 75%),
      radial-gradient(ellipse 18% 30% at 78% 70%, var(--bg-light) 0%, transparent 72%),
      radial-gradient(ellipse 14% 40% at 7% 30%, var(--bg-light) 0%, transparent 75%),
      radial-gradient(ellipse 26% 22% at 22% 82%, var(--bg-mid) 0%, transparent 75%),
      radial-gradient(ellipse 30% 18% at 50% 95%, var(--bg-shadow) 0%, transparent 80%),
      radial-gradient(ellipse 70% 60% at 45% 40%, var(--bg-mid) 0%, transparent 80%),
      linear-gradient(180deg, var(--bg-mid) 0%, var(--bg-shadow) 70%, var(--bg-deep) 100%);
  }
  .hero-shade {
    position: absolute;
    inset: 0;
    background:
      linear-gradient(90deg, rgba(0,0,0,0.25) 0%, transparent 18%, transparent 82%, rgba(0,0,0,0.3) 100%);
  }
  .brand {
    position: absolute;
    left: 161px;
    top: 18px;
    font-weight: 800;
    font-size: 42px;
    letter-spacing: 3px;
    color: var(--text-white);
  }
  .contact-button {
    position: absolute;
    left: 912px;
    top: 15px;
    width: 127px;
    height: 40px;
    border: 2px solid var(--text-white);
    border-radius: 2px;
    display: flex;
    align-items: center;
    justify-content: center;
    font-weight: 600;
    font-size: 16px;
    color: var(--text-white);
    text-decoration: none;
    text-transform: uppercase;
  }
  .signup {
    position: absolute;
    left: 161px;
    top: 256px;
  }
  .signup-headline {
    font-family: "Noto Serif", serif;
    font-weight: 700;
    font-size: 37.5px;
    line-height: 52px;
    width: 820px;
  }
  .signup-form {
    display: flex;
    margin-top: 26px;
  }
  .email-field {
    width: 321px;
    height: 48px;
    border: none;
    border-radius: 2px 0 0 2px;
    background: var(--field-bg);
    padding: 0 15px;
    font-family: "Raleway", sans-serif;
    font-size: 12px;
  }
  .email-field::placeholder { color: var(--placeholder); }
  .send-button {
    width: 130px;
    height: 48px;
    border: none;
    border-radius: 0 2px 2px 0;
    background: var(--accent-purple);
    color: var(--text-white);
    font-family: "Raleway", sans-serif;
    font-weight: 700;
    font-size: 14px;
    letter-spacing: 0.5px;
  }
  .site-footer {
    position: absolute;
    left: 161px;
    right: 161px;
    top: 633px;
    display: flex;
    justify-content: space-between;
    align-items: center;
  }
  .copyright { font-size: 10px; color: var(--text-muted); }
  .social-links { display: flex; gap: 8px; list-style: none; }
  .social-links li {
    width: 25px;
    height: 25px;
    border-radius: 50%;
    background: var(--icon-grey);
    display: flex;
    align-items: center;
    justify-content: center;
  }
  .social-links svg { width: 13px; height: 13px; fill: none; stroke: var(--icon-glyph); stroke-width: 2; stroke-linecap: round; stroke-linejoin: round; }
</style>
</head>
<body>
  <main class="landing">
    <div class="hero-art" role="img" aria-label="Large uncoloured comic line-art background: city towers, a dragon, and a group of heroes, in dark grey tones"></div>
    <div class="hero-shade"></div>

    <div class="brand">ZING</div>
    <a class="contact-button" href="#contact">Contact us</a>

    <section class="signup">
      <h1 class="signup-headline">Lorem ipsum dolor sit amet, consectetur adipisicing elit sed do eiusmod tempor</h1>
      <form class="signup-form" action="#">
        <input class="email-field" type="email" placeholder="Enter your email" aria-label="Email address">
        <button class="send-button" type="submit">SEND</button>
      </form>
    </section>

    <footer class="site-footer">
      <p class="copyright">Copyright © 2014 Zing Webcomic All rights reserved.</p>
      <ul class="social-links" aria-label="Social links">
        <li aria-label="Share"><svg viewBox="0 0 16 16"><circle cx="4" cy="8" r="2"/><circle cx="12" cy="4" r="2"/><circle cx="12" cy="12" r="2"/><path d="M6 7l4-2M6 9l4 2"/></svg></li>
        <li aria-label="Link"><svg viewBox="0 0 16 16"><path d="M7 9l2-2M6 6l-2 2a2.5 2.5 0 0 0 4 4l2-2M10 10l2-2a2.5 2.5 0 0 0-4-4L6 6"/></svg></li>
        <li aria-label="Comments"><svg viewBox="0 0 16 16"><path d="M2 3h12v8H7l-3 3v-3H2z"/></svg></li>
        <li aria-label="Email"><svg viewBox="0 0 16 16"><rect x="2" y="4" width="12" height="9"/><path d="M2 4l6 5 6-5"/></svg></li>
        <li aria-label="Favourite"><svg viewBox="0 0 16 16"><path d="M8 13S2 9.5 2 6a3 3 0 0 1 6-1 3 3 0 0 1 6 1c0 3.5-6 7-6 7z"/></svg></li>
        <li aria-label="Next"><svg viewBox="0 0 16 16"><path d="M3 8h10M9 4l4 4-4 4"/></svg></li>
      </ul>
    </footer>
  </main>
</body>
</html>
```